Vellisant - Quality health delivered at your door

Vellisant offers home and Community Based Services for adults who wish to continue live independently in their communities. We increase accessibility to health care, reduce health care delivery gap, reduce mortality and morbidity, reduce health while promoting healthy living in the comfort of our patients communities or homes.

We provide on site services and deliver high quality healthcare at your door. Our experienced physicians coordinate care with our certified nurse practitioners and provide chronic care management, physical therapy, rehabilitation and medications management.

Target Market(s)

Older population living in independent living facilities

Industry/Entity Type

Health Care

Contact Information for Business Card

Vellisant

Number of Pages Required

4 page

Font styles to use
Sans Serif

Colors

Designer to choose colors to be used in the design.

```html
<!DOCTYPE html>
<html lang="en">
<head>
<meta charset="utf-8">
<title>Vellisant - Quality health delivered at your door</title>
<link rel="stylesheet" href="https://fonts.googleapis.com/css2?family=Raleway:ital,wght@0,400;0,500;0,600;0,700;0,800;1,400&display=swap">
<style>
:root{
  --orange:#f7941d;
  --orange-dark:#f08a0b;
  --green:#5f8a17;
  --green-dark:#496d0f;
  --footer:#193300;
  --footer-text:#e7ecdf;
  --ink:#13200a;
  --text:#444;
  --white:#fff;
  --grey-dot:#4a4f58;
}
*{box-sizing:border-box;margin:0;padding:0}
html,body{width:1200px;height:2553px;overflow:hidden}
body{position:relative;font-family:"Raleway",sans-serif;color:var(--text);background:var(--white)}
.abs{position:absolute}
a{color:inherit;text-decoration:none}

/* header */
.topline{left:0;top:0;width:1200px;height:5px;background:var(--orange)}
.phone-tab{left:887px;top:0;width:236px;height:46px;background:var(--orange);border-radius:0 0 6px 14px;color:#fff;font-weight:700;font-size:17px;display:flex;align-items:center;justify-content:center;gap:12px}
.brand{left:75px;top:14px;width:152px;text-align:center}
.brand-dot{width:80px;height:80px;border-radius:50%;background:var(--orange);margin:0 auto;border:4px solid var(--green-dark)}
.brand-name{font-size:22px;font-weight:600;color:var(--ink);letter-spacing:.5px;margin-top:4px}
.nav{left:0;top:93px;width:1200px;font-size:12.5px;font-weight:700;color:var(--ink)}
.nav a{position:absolute;white-space:nowrap}
.nav .active{color:var(--green)}

/* hero */
.hero{left:0;top:141px;width:1200px;height:519px;background:linear-gradient(90deg,#e9e8f2 0%,#eceaf3 35%,#e4e6ee 100%)}
.hero-photo{left:420px;top:141px;width:780px;height:519px;background:linear-gradient(90deg,rgba(233,232,242,0) 0%,#d9d3cf 25%,#cfd6e6 60%,#6f9ad6 85%,#e3e6ec 100%)}
.hero-title{left:75px;top:300px;width:520px;font-size:18.5px;font-weight:800;line-height:27px;color:var(--ink);text-transform:uppercase}
.btn{display:flex;align-items:center;justify-content:center;background:var(--orange);color:#fff;font-weight:700;font-size:14px;text-transform:uppercase}
.hero-btn{left:75px;top:400px;width:179px;height:44px}
.dots{display:flex;gap:8px}
.dots span{width:12px;height:12px;background:var(--grey-dot)}
.dots span.on{background:var(--green)}
.hero-dots{left:75px;top:476px}

/* welcome */
.section-title{left:0;width:1200px;text-align:center;font-size:25px;font-weight:700;color:var(--ink);text-transform:uppercase}
.rule{height:3px;width:70px;background:var(--orange)}
.center-rule{left:565px}
.welcome-text{left:70px;top:778px;width:1060px;text-align:center;font-size:14px;line-height:23px}

/* services */
.services{left:0;top:905px;width:1200px;height:460px;background:var(--green)}
.services-lead{left:0;top:1032px;width:1200px;text-align:center;font-size:14.5px;color:#f0f4e6}
.service{top:1080px;width:260px;text-align:center;color:#fff;font-size:17.5px;font-weight:600}
.service-icon{width:94px;height:94px;border-radius:50%;background:var(--orange);border:3px solid #fff;margin:0 auto 18px;display:flex;align-items:center;justify-content:center}
.services-btn{left:495px;top:1273px;width:210px;height:46px}

/* testimonial */
.testimonial{left:0;top:1365px;width:1200px;height:368px;background:#ebe7ea}
.testimonial-photo{left:660px;top:1365px;width:540px;height:368px;background:linear-gradient(90deg,rgba(235,231,234,0) 0%,#c9dde8 25%,#e6d2c8 55%,#efc9c4 80%,#cfe0ea 100%)}
.left-title{left:75px;font-size:25px;font-weight:700;color:var(--ink);text-transform:uppercase}
.quote-mark{left:75px;top:1497px;width:40px;height:40px;border-radius:50%;background:var(--green);color:#fff;font-size:30px;font-weight:800;display:flex;align-items:center;justify-content:center;line-height:1}
.quote-text{left:138px;top:1500px;width:480px;font-style:italic;font-size:14.5px;line-height:26px;color:#333}
.quote-name{left:138px;top:1612px;font-size:11.5px;font-weight:700;color:var(--orange-dark)}
.round-dots span{border-radius:50%;width:9px;height:9px;background:#8a8d94}
.round-dots span.on{background:#1b1b1b}

/* blog */
.post{top:1859px;width:330px}
.post-photo{width:330px;height:204px}
.post-title{margin-top:22px;font-size:16px;font-weight:700;color:var(--ink);text-transform:uppercase}
.post-text{margin-top:8px;font-size:13.5px;line-height:21.5px;color:#444}
.post-more{margin-top:10px;font-size:10.5px;font-weight:700;color:var(--orange);text-transform:uppercase}

/* footer */
.site-footer{color:var(--footer-text)}
.footer{left:0;top:2281px;width:1200px;height:272px;background:var(--footer)}
.footer-logo{left:560px;top:2250px;width:80px;height:80px;border-radius:50%;background:var(--orange);border:4px solid var(--green-dark)}
.footer-name{left:450px;top:2328px;width:300px;text-align:center;font-size:22px;font-weight:600;color:#fff}
.copyright{left:450px;top:2380px;width:300px;text-align:center;font-size:11.5px;line-height:19px;color:#dfe6d4}
.f-head{font-size:12.5px;font-weight:700;color:var(--orange);text-transform:uppercase}
.f-list{list-style:none;margin-top:14px;font-size:12.5px;color:var(--footer-text)}
.f-list li{height:26px;display:flex;align-items:center;gap:14px}
.f-ico{width:14px;display:inline-flex;justify-content:center}
.f-address{margin-top:14px;font-size:12.5px;line-height:19px;color:var(--footer-text)}
.news-text{margin-top:10px;width:200px;font-size:12px;line-height:19px;color:#dfe6d4}
.news-input{left:752px;top:2405px;width:194px;height:36px;background:#fff;color:#777;font-size:11px;padding-left:14px;display:flex;align-items:center}
.news-btn{left:870px;top:2451px;width:76px;height:31px;background:var(--green);color:#fff;font-size:12px;font-weight:700;display:flex;align-items:center;justify-content:center}
.social-box{width:11px;height:11px;background:var(--footer-text);display:inline-block}
</style>
</head>
<body>

<header>
  <div class="abs topline"></div>
  <div class="abs phone-tab">
    <svg width="15" height="15" viewBox="0 0 24 24" aria-hidden="true"><path fill="#fff" d="M6.6 10.8a15.1 15.1 0 0 0 6.6 6.6l2.2-2.2c.3-.3.7-.4 1-.2 1.1.4 2.3.6 3.6.6.6 0 1 .4 1 1V20c0 .6-.4 1-1 1C10.6 21 3 13.4 3 4c0-.6.4-1 1-1h3.5c.6 0 1 .4 1 1 0 1.3.2 2.5.6 3.6.1.3 0 .7-.2 1z"/></svg>
    1-800-555-0142
  </div>
  <div class="abs brand">
    <div class="brand-dot"></div>
    <div class="brand-name">VELLISANT</div>
  </div>
  <nav class="abs nav">
    <a class="active" style="left:521px">HOME</a>
    <a style="left:604px">ABOUT US</a>
    <a style="left:717px">SERVICES</a>
    <a style="left:824px">BLOG</a>
    <a style="left:905px">LATEST NEWS</a>
    <a style="left:1042px">CONTACT US</a>
  </nav>
</header>

<section>
  <div class="abs hero"></div>
  <div class="abs hero-photo" role="img" aria-label="Photo of a nurse in blue scrubs caring for a smiling elderly woman with a walking cane"></div>
  <h1 class="abs hero-title">Vellisant offers home and community based services for adults who wish to continue live independently in their communities</h1>
  <a class="abs btn hero-btn">Read More</a>
  <div class="abs dots hero-dots"><span class="on"></span><span></span><span></span><span></span></div>
</section>

<section>
  <h2 class="abs section-title" style="top:701px">Welcome to our website</h2>
  <div class="abs rule center-rule" style="top:751px"></div>
  <p class="abs welcome-text">Vellisant offers home and Community Based Services for adults who wish to continue to live independently in the comfort of their communities. We provide on site services and deliver high quality healthcare at your door. Our experienced physicians coordinate care with our certified nurse practitioners and provide chronic care management, physical therapy, rehabilitation and medications management.</p>
</section>

<section>
  <div class="abs services"></div>
  <h2 class="abs section-title" style="top:954px;color:#fff">Our Services</h2>
  <div class="abs rule center-rule" style="top:997px"></div>
  <p class="abs services-lead">Vellisant offers home and Community Based Services for adults who wish to continue live independently in their communities.</p>

  <div class="abs service" style="left:66px">
    <div class="service-icon"><svg width="40" height="40" viewBox="0 0 40 40" aria-hidden="true"><circle cx="20" cy="12" r="7" fill="#fff"/><path d="M7 36c0-8 6-13 13-13s13 5 13 13z" fill="#fff"/><path d="M18 27h4v3h3v4h-3v3h-4v-3h-3v-4h3z" fill="#f7941d"/></svg></div>
    Home Health Assistance
  </div>
  <div class="abs service" style="left:333px">
    <div class="service-icon"><svg width="40" height="40" viewBox="0 0 40 40" aria-hidden="true"><circle cx="12" cy="12" r="4" fill="#fff"/><rect x="5" y="24" width="30" height="4" fill="#fff"/><rect x="8" y="28" width="3" height="6" fill="#fff"/><rect x="29" y="28" width="3" height="6" fill="#fff"/><path d="M10 22l8-6h10l4 6z" fill="#fff"/></svg></div>
    Physical Therapy
  </div>
  <div class="abs service" style="left:604px">
    <div class="service-icon"><svg width="40" height="40" viewBox="0 0 40 40" aria-hidden="true"><path d="M20 5c-8 0-13 6-13 12 0 4 2 6 3 8v10h12v-5h5c2 0 3-1 3-3v-4h3l-3-6c0-7-4-12-10-12z" fill="#fff"/><circle cx="19" cy="16" r="5" fill="none" stroke="#f7941d" stroke-width="2"/></svg></div>
    Mental Health
  </div>
  <div class="abs service" style="left:874px">
    <div class="service-icon"><svg width="40" height="40" viewBox="0 0 40 40" aria-hidden="true"><path d="M12 8c4-2 6 0 8 0s4-2 8 0 4 8 2 12c-1 3-1 8-3 12-1 2-3 1-3-1l-1-6c0-2-2-2-2 0l-1 6c0 2-2 3-3 1-2-4-2-9-3-12-2-4-2-10 0-12z" fill="#fff"/></svg></div>
    Dental Health
  </div>
  <a class="abs btn services-btn">View All Services</a>
</section>

<section>
  <div class="abs testimonial"></div>
  <div class="abs testimonial-photo" role="img" aria-label="Photo of a smiling elderly couple embracing, cheek to cheek"></div>
  <h2 class="abs left-title" style="top:1412px">What our client says</h2>
  <div class="abs rule" style="left:75px;top:1463px"></div>
  <div class="abs quote-mark">&#8220;</div>
  <p class="abs quote-text">Lorem ipsum dolor sit amet, consect- etuer adipiscing elit, sed diam nonummy nibh euismod tincidunt ut laoreet dolore magna aliquam erat volutpat. Ut wisi enim ad minim veniam, quis nostrud exerci tation ullam..."</p>
  <div class="abs quote-name">-NAME HEADING</div>
  <div class="abs dots round-dots" style="left:75px;top:1672px"><span class="on"></span><span></span><span></span><span></span></div>
</section>

<section>
  <h2 class="abs section-title" style="top:1773px">Blog Posts</h2>
  <div class="abs rule center-rule" style="top:1824px"></div>

  <article class="abs post" style="left:75px">
    <div class="post-photo" role="img" aria-label="Photo of a smiling senior couple" style="background:linear-gradient(135deg,#9ab7a8,#c88a7e 55%,#e7b7b4)"></div>
    <h3 class="post-title">Lorem ipsum dolor sit amet</h3>
    <p class="post-text">Etuer adipiscing elit, sed diam nonummy nibh euismod tincidunt ut laoreet dolore magna aliquam erat volutpat...</p>
    <div class="post-more">Continue Reading</div>
  </article>
  <article class="abs post" style="left:436px">
    <div class="post-photo" role="img" aria-label="Photo of a group of cheerful seniors outdoors" style="background:linear-gradient(135deg,#7fa35a,#c9c5b8 50%,#7aa0b8)"></div>
    <h3 class="post-title">Lorem ipsum dolor sit amet</h3>
    <p class="post-text">Etuer adipiscing elit, sed diam nonummy nibh euismod tincidunt ut laoreet dolore magna aliquam erat volutpat...</p>
    <div class="post-more">Continue Reading</div>
  </article>
  <article class="abs post" style="left:797px">
    <div class="post-photo" role="img" aria-label="Photo of an elderly couple hugging in a park" style="background:linear-gradient(135deg,#5e8a3a,#d8cfc6 50%,#4e7a34)"></div>
    <h3 class="post-title">Lorem ipsum dolor sit amet</h3>
    <p class="post-text">Etuer adipiscing elit, sed diam nonummy nibh euismod tincidunt ut laoreet dolore magna aliquam erat volutpat...</p>
    <div class="post-more">Continue Reading</div>
  </article>
</section>

<footer class="site-footer">
  <div class="abs footer"></div>
  <div class="abs footer-logo"></div>
  <div class="abs footer-name">VELLISANT</div>
  <div class="abs copyright">Copyright © 2017. Company Name<br>All Right Reserved</div>

  <div class="abs" style="left:75px;top:2330px">
    <div class="f-head">Site Map</div>
    <ul class="f-list">
      <li>Home</li><li>About Us</li><li>Services</li><li>Blog</li><li>Latest News</li><li>Contact Us</li>
    </ul>
  </div>

  <div class="abs" style="left:269px;top:2330px;width:200px">
    <div class="f-head">Contact Info</div>
    <p class="f-address">2240 Larkfield<br>Road, Glasgow, G12 8QT</p>
    <ul class="f-list" style="margin-top:6px">
      <li><span class="f-ico"><svg width="12" height="12" viewBox="0 0 24 24" aria-hidden="true"><path fill="#e7ecdf" d="M6.6 10.8a15.1 15.1 0 0 0 6.6 6.6l2.2-2.2c.3-.3.7-.4 1-.2 1.1.4 2.3.6 3.6.6.6 0 1 .4 1 1V20c0 .6-.4 1-1 1C10.6 21 3 13.4 3 4c0-.6.4-1 1-1h3.5c.6 0 1 .4 1 1 0 1.3.2 2.5.6 3.6.1.3 0 .7-.2 1z"/></svg></span>1-800-555-0142</li>
      <li><span class="f-ico"><svg width="13" height="10" viewBox="0 0 26 20" aria-hidden="true"><rect width="26" height="20" rx="2" fill="#e7ecdf"/><path d="M1 2l12 9 12-9" stroke="#193300" stroke-width="2" fill="none"/></svg></span>info@vellisant-care.com</li>
      <li><span class="f-ico"><svg width="13" height="12" viewBox="0 0 26 24" aria-hidden="true"><path d="M1 24l24-12L1 0v9l16 3-16 3z" fill="#e7ecdf"/></svg></span>Map Direction</li>
    </ul>
  </div>

  <div class="abs" style="left:752px;top:2330px">
    <div class="f-head">Enail Newsletter</div>
    <p class="news-text">Consectetuer adipiscing elit, sed diam nonummy nibh...</p>
  </div>
  <div class="abs news-input">Enter Email Address</div>
  <div class="abs news-btn">SIGN UP</div>

  <div class="abs" style="left:1004px;top:2330px">
    <div class="f-head">Connect Us</div>
    <ul class="f-list" style="margin-top:10px">
      <li style="height:32px"><span class="social-box"></span>Kinnectly</li>
      <li style="height:32px"><span class="social-box"></span>Chirpsy</li>
      <li style="height:32px"><span class="social-box"></span>Workmesh</li>
      <li style="height:32px"><span class="social-box"></span>Orbitly +</li>
      <li style="height:32px"><span class="social-box"></span>Viewcast</li>
    </ul>
  </div>
</footer>

</body>
</html>
```